I need a business card designed using the logo provided either vertical or horizontal......Harbourline Property Group is an Australian based real estate company that caters for the upper end of the market so the design of the business card "must reflect" the companies image!!
Colour combinations are optional but "must be realistic" and must be able to be accurately useable CMYK colours.
Please consider that any colours used "must be able to be used" and be suitable in following designs for "pull out banner signs" and "real estate signs".
The colours and the font in the attached designs are for example and other combinations are encouraged.
Target Market(s)
The High End of the Australian real estate market
Industry/Entity Type
Business
Contact Information for Business Card
Logo - Business Name - Director + Licensed Real Estate Agent - Mobile Number (Cell Phone) - Business Number - Fax - Email Address - Web address
Requirements
Must have
- Designs and colours (CMYK) that can easily be interpreted by an Australian printer.
Nice to have
- Some alternative ideas on colour and font..........the ones provided are ok and have been provided as an example but I am looking for alternative ideas
Should not have
- Loud, overly bright colours. Designs that do not reflect the professional standards of the business.
- Designs that look good on a computer monitor but can not be re-created on a printing press.............this is most important when it comes to shading etc.

```html
<!DOCTYPE html>
<html lang="en">
<head>
<meta charset="utf-8">
<title>Harbourline Property Group – Business Card</title>
<link href="https://fonts.googleapis.com/css2?family=Lato:wght@400;700&display=swap" rel="stylesheet">
<style>
  :root {
    --backdrop: #8a8a8a;
    --card: #141414;
    --card-edge: #1b1b1b;
    --gold-pale: #d8c98f;
    --gold-deep: #c38f35;
    --text-light: #d6d6d6;
    --text-soft: #c9c9c9;
  }
  * { margin: 0; padding: 0; box-sizing: border-box; }
  html, body {
    width: 1200px;
    height: 900px;
    overflow: hidden;
    background: var(--backdrop);
    font-family: "Lato", Arial, sans-serif;
  }
  .canvas {
    position: relative;
    width: 1200px;
    height: 900px;
  }
  .card {
    position: absolute;
    left: 310px;
    width: 580px;
    height: 336px;
    border-radius: 18px;
    background: linear-gradient(135deg, var(--card-edge), var(--card));
    overflow: hidden;
  }
  .card--front { top: 111px; }
  .card--back { top: 482px; }

  .brand {
    position: absolute;
    display: flex;
    flex-direction: column;
    align-items: center;
    text-align: center;
  }
  .brand__mark {
    width: 18px;
    height: 18px;
    background: var(--gold-deep);
    margin-bottom: 14px;
  }
  .brand__name {
    font-weight: 700;
    color: var(--text-light);
    letter-spacing: 0.08em;
    text-transform: uppercase;
    line-height: 1.25;
  }
  .card--front .brand {
    left: 40px;
    top: 118px;
    width: 230px;
  }
  .card--front .brand__name { font-size: 19px; }

  .card--back .brand {
    left: 0;
    right: 0;
    top: 122px;
  }
  .card--back .brand__name {
    font-size: 24px;
    color: var(--gold-pale);
  }

  .contact {
    position: absolute;
    left: 300px;
    top: 118px;
  }
  .contact__name {
    font-size: 28px;
    font-weight: 400;
    line-height: 1.1;
    color: var(--gold-pale);
  }
  .contact__surname { color: var(--gold-deep); }
  .contact__role {
    font-size: 17px;
    color: var(--text-soft);
    margin-top: 2px;
  }
  .contact__details {
    list-style: none;
    margin-top: 20px;
    margin-left: 4px;
    font-size: 17px;
    line-height: 1.3;
    color: var(--text-soft);
  }
</style>
</head>
<body>
<main class="canvas">
  <section class="card card--front">
    <div class="brand">
      <span class="brand__mark"></span>
      <p class="brand__name">Harbourline<br>Property Group</p>
    </div>
    <div class="contact">
      <h1 class="contact__name">Daniel <span class="contact__surname">Mercer</span></h1>
      <p class="contact__role">Managing Director</p>
      <ul class="contact__details">
        <li>info@harbourline.com.au</li>
        <li>044-987 654 321</li>
      </ul>
    </div>
  </section>

  <section class="card card--back">
    <div class="brand">
      <span class="brand__mark"></span>
      <p class="brand__name">Harbourline Property Group</p>
    </div>
  </section>
</main>
</body>
</html>
```